Stage Design Company Business Card

We are looking to step up up our business card design for our team.

We are a Full service Design and Consultation company for Stage and TV with an emphasis in Theatrical Lighting.

We like our materials to be clean and modern with solid colors free of patterns and gradients. Our brand consists of 4 primary colors Purple, Black, Grey, and White. Provided is our Word Mark as well as our Symbol Logo.

We would like our cards to leave an impression beyond the information, show our attention to design and detail, and make our marks an easily recognized feature (together or apart) for our clients.

We need a warm approachable comfortable feel for some clients, and a professional flair for the board member type clients.

Attached are our brand elements, and our existing cards to give a sense of our style and a glipse at the information we provide on our cards.

Target Market(s)

broad client base from church leaders to high school teachers and architects.

Industry/Entity Type

Business

Contact Information for Business Card

We format our phone number with periods not parenthesis or dashes. Information will be edited for each of our team members, and team member specific cards are not part of this scope, but rather a template so to speak.

Font styles to use
Sans Serif

Colors
6b449b
ffffff
000000
333333
aaaaaa

Requirements
Must have
• Wordmark and logo mark present (does not need to exist on the same side of card)
• Brand Colors,
• Name, Phone, Email, Address.
• Unique choices that make someone stop and take a second look
Nice to have
• It would be nice to somehow convey what we DO, as our brand name does not lend itself to this, outside of an obvious tagline though.....
• social media if not crowded. all of our handles match (instagram, twitter, facebook)
Should not have
• "clipart"

```html
<!DOCTYPE html>
<html lang="en">
<head>
<meta charset="utf-8">
<title>Corwin Business Card</title>
<link rel="stylesheet" href="https://fonts.googleapis.com/css2?family=Source+Sans+3:wght@400;600&display=swap">
<style>
  :root {
    --ink: #3a3a36;
    --accent: #6b449b;
    --paper: #ffffff;
    --backdrop: #e8e6e3;
    --on-ink: #ffffff;
  }
  * { margin: 0; padding: 0; box-sizing: border-box; }
  html, body {
    width: 1200px;
    height: 899px;
    overflow: hidden;
    background: var(--backdrop);
    font-family: "Source Sans 3", sans-serif;
  }
  .canvas { position: relative; width: 1200px; height: 899px; }

  .card {
    position: absolute;
    background: var(--paper);
    box-shadow: 0 6px 18px rgba(0,0,0,0.18);
    overflow: hidden;
  }
  .card-front { left: 77px; top: 34px; width: 588px; height: 362px; }
  .card-back  { left: 388px; top: 505px; width: 566px; height: 351px; }

  /* front */
  .front-band {
    position: absolute;
    left: 0; top: 59px;
    width: 467px; height: 246px;
    background: var(--ink);
    color: var(--on-ink);
    padding: 27px 0 0 34px;
  }
  .front-accent {
    position: absolute;
    left: 467px; top: 59px;
    width: 6px; height: 246px;
    background: var(--accent);
  }
  .person-name { font-size: 24px; font-weight: 400; line-height: 1.1; }
  .person-role { font-size: 15px; margin-top: 2px; }
  .address { font-size: 15px; line-height: 1.35; margin-top: 18px; }
  .contact-list { list-style: none; margin-top: 16px; font-size: 15px; line-height: 1.45; }
  .contact-list li { display: flex; align-items: center; gap: 9px; }
  .contact-list svg { width: 12px; height: 12px; fill: var(--on-ink); flex: none; }

  .front-mark {
    position: absolute;
    left: 473px; top: 138px;
    width: 115px;
    display: flex; flex-direction: column; align-items: center; gap: 12px;
    color: var(--ink);
  }
  .mark-dot { width: 40px; height: 40px; border-radius: 50%; background: var(--accent); }
  .mark-name { font-size: 19px; font-weight: 600; letter-spacing: 0.14em; margin-right: -0.14em; }

  /* back */
  .back-band {
    position: absolute; left: 0; width: 100%; height: 40px; background: var(--ink);
  }
  .back-band-top { top: 0; }
  .back-band-bottom { bottom: 0; height: 41px; }
  .back-rule {
    position: absolute; left: 0; width: 100%; height: 5px; background: var(--accent);
  }
  .back-rule-top { top: 40px; }
  .back-rule-bottom { bottom: 41px; }
  .back-mark {
    position: absolute;
    left: 0; right: 0; top: 82px;
    display: flex; flex-direction: column; align-items: center; gap: 34px;
    color: var(--ink);
  }
  .back-mark .mark-dot { width: 96px; height: 96px; }
  .back-mark .mark-name { font-size: 40px; letter-spacing: 0.5em; margin-right: -0.5em; }
</style>
</head>
<body>
<main class="canvas">

  <section class="card card-front" aria-label="Business card front">
    <div class="front-band">
      <h1 class="person-name">Marcus Hale</h1>
      <p class="person-role">Managing Director</p>
      <p class="address">12345, Address Goes Here<br>Country Name, 123456.</p>
      <ul class="contact-list">
        <li>
          <svg viewBox="0 0 24 24" aria-hidden="true"><path d="M6.6 10.8a15.1 15.1 0 0 0 6.6 6.6l2.2-2.2a1 1 0 0 1 1-.25 11.4 11.4 0 0 0 3.6.6 1 1 0 0 1 1 1V20a1 1 0 0 1-1 1A17 17 0 0 1 3 4a1 1 0 0 1 1-1h3.5a1 1 0 0 1 1 1c0 1.25.2 2.45.6 3.6a1 1 0 0 1-.25 1z"/></svg>
          044.555.010.247
        </li>
        <li>
          <svg viewBox="0 0 24 24" aria-hidden="true"><path d="M2 5h20v14H2z"/><path d="M3 6l9 7 9-7" fill="none" stroke="#3a3a36" stroke-width="2"/></svg>
          hello@corwinstage.com
        </li>
        <li>
          <svg viewBox="0 0 24 24" aria-hidden="true"><path d="M10.6 13.4a1 1 0 0 1 0-1.4l3-3a1 1 0 1 1 1.4 1.4l-3 3a1 1 0 0 1-1.4 0zM8 20a4 4 0 0 1-2.8-6.8l2.5-2.5 1.4 1.4-2.5 2.5a2 2 0 0 0 2.8 2.8l2.5-2.5 1.4 1.4-2.5 2.5A4 4 0 0 1 8 20zm8.3-6.7-1.4-1.4 2.5-2.5a2 2 0 0 0-2.8-2.8l-2.5 2.5-1.4-1.4 2.5-2.5a4 4 0 0 1 5.6 5.6z"/></svg>
          www.corwinstage.com
        </li>
      </ul>
    </div>
    <div class="front-accent"></div>
    <div class="front-mark">
      <span class="mark-dot"></span>
      <span class="mark-name">CORWIN</span>
    </div>
  </section>

  <section class="card card-back" aria-label="Business card back">
    <div class="back-band back-band-top"></div>
    <div class="back-rule back-rule-top"></div>
    <div class="back-mark">
      <span class="mark-dot"></span>
      <span class="mark-name">CORWIN</span>
    </div>
    <div class="back-rule back-rule-bottom"></div>
    <div class="back-band back-band-bottom"></div>
  </section>

</main>
</body>
</html>
```